Colin Vardek Business card

Hey there, I’m hoping to have a business card designed. I’m in Real estate and just switched to a new Brokerage called: The Harbourline Property Group

The back could just be the company name maybe or whatever looks good!

I’ve attached some logos of our company and some cards my buddy had done up.

On the card:
Colin Vardek
colinvardek@mailora.com
587-412-9065
colinvardek.ca

Target Market(s)

Home buyers and sellers

Industry/Entity Type

Real Estate

Contact Information for Business Card

just looking for a cool and modern design with my picture on it. I like the idea of Black and red being used.

Requirements
Must have
• all the details provided. I'm open to anything. Just want a professional looking card.

```html
<!DOCTYPE html>
<html lang="en">
<head>
<meta charset="utf-8">
<title>Colin Vardek – Business Card</title>
<link rel="stylesheet" href="https://fonts.googleapis.com/css2?family=Roboto:wght@400;500;900&display=swap">
<style>
  :root {
    --bg: #2a2a2c;
    --brand-red: #cf1f3c;
    --brand-red-deep: #b0142f;
    --ink: #1f1d22;
    --paper: #ffffff;
    --photo-light: #e9e4e0;
    --photo-dark: #3a3d47;
  }
  * { margin: 0; padding: 0; box-sizing: border-box; }
  html, body { width: 1200px; height: 852px; overflow: hidden; }
  body {
    background: var(--bg);
    font-family: "Roboto", sans-serif;
    position: relative;
  }
  .card {
    position: absolute;
    top: 272px;
    width: 540px;
    height: 308px;
    border-radius: 22px;
    overflow: hidden;
    box-shadow: 0 14px 30px rgba(0,0,0,.45);
  }
  .brand-name {
    font-weight: 900;
    text-transform: uppercase;
    letter-spacing: -0.5px;
    white-space: nowrap;
  }

  /* Back side */
  .card--back {
    left: 40px;
    background: var(--brand-red);
    display: flex;
    align-items: center;
    justify-content: center;
  }
  .card--back .brand-name {
    color: var(--brand-red-deep);
    font-size: 40px;
    line-height: 1.05;
    text-align: center;
  }

  /* Front side */
  .card--front {
    left: 620px;
    background: var(--paper);
    border-bottom: 6px solid var(--brand-red);
  }
  .card--front .brand-name {
    position: absolute;
    left: 30px;
    top: 84px;
    color: var(--ink);
    font-size: 25px;
    line-height: 1.1;
  }
  .portrait {
    position: absolute;
    right: 26px;
    top: 0;
    width: 220px;
    height: 176px;
    background: linear-gradient(180deg, var(--photo-light) 0%, var(--photo-dark) 100%);
  }
  .info-band {
    position: absolute;
    left: 140px;
    right: 0;
    top: 176px;
    height: 100px;
    background: var(--brand-red);
    clip-path: polygon(16px 0, 100% 0, 100% 100%, 0 100%, 0 40px);
  }
  .agent-name {
    position: absolute;
    right: 40px;
    top: 14px;
    color: var(--paper);
    font-weight: 500;
    font-size: 20px;
  }
  .contact-list {
    position: absolute;
    left: 28px;
    top: 34px;
    list-style: none;
    color: var(--paper);
    font-size: 14px;
    line-height: 1.45;
  }
  .contact-list li { display: flex; align-items: center; gap: 7px; }
  .contact-list svg { width: 12px; height: 12px; flex: none; }
  .corner-mark {
    position: absolute;
    left: 30px;
    bottom: 22px;
    width: 36px;
    height: 36px;
    background: var(--brand-red);
  }
</style>
</head>
<body>

  <section class="card card--back" aria-label="Card back">
    <p class="brand-name">The Harbourline<br>Property Group</p>
  </section>

  <section class="card card--front" aria-label="Card front">
    <p class="brand-name">The Harbourline<br>Property Group</p>

    <div class="portrait" role="img" aria-label="Portrait photo of Colin Vardek in a dark blazer and white shirt"></div>

    <div class="info-band">
      <p class="agent-name">Colin Vardek</p>
      <ul class="contact-list">
        <li>
          <svg viewBox="0 0 12 12" aria-hidden="true"><circle cx="6" cy="6" r="6" fill="#fff"/><path d="M3.6 3.2l1.2-.4.7 1.5-.8.6c.4.8 1 1.4 1.8 1.8l.6-.8 1.5.7-.4 1.2C6 7.8 4.2 6 3.6 3.2z" fill="#cf1f3c"/></svg>
          <span>587-412-9065</span>
        </li>
        <li>
          <svg viewBox="0 0 12 12" aria-hidden="true"><circle cx="6" cy="6" r="6" fill="#fff"/><rect x="3" y="4" width="6" height="4.2" fill="none" stroke="#cf1f3c" stroke-width=".9"/><path d="M3 4l3 2.3L9 4" fill="none" stroke="#cf1f3c" stroke-width=".9"/></svg>
          <span>colinvardek@mailora.com</span>
        </li>
        <li>
          <svg viewBox="0 0 12 12" aria-hidden="true"><circle cx="6" cy="6" r="6" fill="#fff"/><circle cx="6" cy="6" r="3.2" fill="none" stroke="#cf1f3c" stroke-width=".8"/><path d="M2.8 6h6.4M6 2.8c-1.6 1.8-1.6 4.6 0 6.4M6 2.8c1.6 1.8 1.6 4.6 0 6.4" fill="none" stroke="#cf1f3c" stroke-width=".7"/></svg>
          <span>colinvardek.ca</span>
        </li>
      </ul>
    </div>

    <div class="corner-mark" aria-hidden="true"></div>
  </section>

</body>
</html>
```